Kestrel Home Business Card Design

We need a business card for a Building company based in Queensland, Australia. Our colours are orange black and we do base all our homes design names and other aspect of our business on astrology. We want the consumer to perceive the company as professional and to attract investors to our company.We have over 20 years in the building industry.We pride ourselves on our innovation of designs and making the building process for anyone from families to investor a smooth and simple experience.
Business
Amelia Prichard0411752116PO Box 454, Mudgeerbaameliaprichard@zodiachomes.com

```html
<!DOCTYPE html>
<html lang="en">
<head>
<meta charset="utf-8">
<title>Kestrel Homes – Business Card</title>
<link rel="stylesheet" href="https://fonts.googleapis.com/css2?family=Lato:wght@400;700;900&display=swap">
<style>
  :root {
    --backdrop: #2a2a2a;
    --paper: #ffffff;
    --paper-shade: #ececec;
    --ink: #151515;
    --card-dark: #1e1b1c;
    --orange: #e8901a;
    --muted: #d4d4d4;
  }
  * { box-sizing: border-box; margin: 0; padding: 0; }
  html, body {
    width: 1200px; height: 873px; overflow: hidden;
    background: var(--backdrop);
    font-family: "Lato", sans-serif;
  }
  .business-card {
    position: absolute; left: 150px; top: 182px;
    width: 900px; height: 510px;
    background: var(--card-dark);
    box-shadow: 0 18px 40px rgba(0,0,0,.55);
    overflow: hidden;
  }
  .brand-panel {
    position: absolute; left: 0; top: 0; width: 100%; height: 210px;
    background: linear-gradient(180deg, var(--paper) 0%, var(--paper) 55%, var(--paper-shade) 100%);
    display: flex; flex-direction: column; align-items: center; justify-content: center; gap: 14px;
    padding-top: 8px;
  }
  .brand-mark {
    width: 78px; height: 78px; border-radius: 50%;
    background: var(--orange);
  }
  .brand-name {
    font-weight: 900; font-size: 44px; color: var(--ink); letter-spacing: .5px; line-height: 1;
  }
  .divider {
    position: absolute; left: 0; top: 210px; width: 100%; height: 7px; background: var(--orange);
  }
  .pointer {
    position: absolute; left: 58px; top: 216px;
  }
  .holder {
    position: absolute; left: 60px; top: 248px;
  }
  .holder-name { font-weight: 700; font-size: 30px; color: var(--orange); line-height: 1.1; }
  .holder-role { font-size: 21px; color: var(--muted); margin-top: 4px; }
  .address {
    position: absolute; left: 60px; top: 370px;
    font-size: 21px; font-style: normal; color: var(--muted); line-height: 1.55;
  }
  .contact {
    position: absolute; right: 50px; top: 246px;
    list-style: none; text-align: right;
  }
  .contact li {
    display: flex; align-items: center; justify-content: flex-end; gap: 14px;
    font-size: 21px; color: var(--muted); margin-bottom: 14px;
  }
  .contact svg { flex: none; }
  .base-stripe {
    position: absolute; left: 0; bottom: 26px; width: 100%; height: 7px; background: var(--orange);
  }
</style>
</head>
<body>
  <article class="business-card">
    <header class="brand-panel">
      <span class="brand-mark" aria-hidden="true"></span>
      <h1 class="brand-name">Kestrel Homes</h1>
    </header>
    <div class="divider"></div>
    <svg class="pointer" width="30" height="16" viewBox="0 0 30 16" aria-hidden="true">
      <polygon points="0,0 30,0 15,15" fill="#e8901a"/>
      <polygon points="8,0 22,0 15,7" fill="#ffffff"/>
    </svg>
    <section class="holder">
      <p class="holder-name">Harriet Colvane</p>
      <p class="holder-role">CEO &amp; Managing Director</p>
    </section>
    <address class="address">PO Box 872,<br>Tallowridge</address>
    <ul class="contact">
      <li>0487309625
        <svg width="14" height="20" viewBox="0 0 14 20" aria-hidden="true"><rect x="1.5" y="1.5" width="11" height="17" rx="2" fill="none" stroke="#e8901a" stroke-width="2"/></svg>
      </li>
      <li>harrietcolvane@kestrelhomes.example
        <svg width="18" height="13" viewBox="0 0 18 13" aria-hidden="true"><rect width="18" height="13" fill="#e8901a"/><polyline points="0,0 9,7 18,0" fill="none" stroke="#1e1b1c" stroke-width="1.5"/></svg>
      </li>
    </ul>
    <div class="base-stripe"></div>
  </article>
</body>
</html>
```